Business Card Design Project

I require a business card with the following information on them for various different people;
name
m:
f:
e:
I have a logo already and will attached that. We are in the construction industry. I require something clean and simple but eye catching at the same time. You can use another colour with our logo if you like and you can style the logo as well if you wish. I am open.
Also it needs to be front and back design.
Industry/Entity Type
Construction
Requirements
Must have
- Logo, name, mobile, fax and email address.
Front and back design

```html
<!DOCTYPE html>
<html lang="en">
<head>
<meta charset="utf-8">
<title>Northfield Builders – Business Card, Front and Back</title>
<link rel="stylesheet" href="https://fonts.googleapis.com/css2?family=Questrial&family=Arimo:wght@400&display=swap">
<style>
  :root {
    --page-bg: #1c1c1c;
    --card-top: #5a5a58;
    --card-bottom: #3e3e3d;
    --card-edge: #6b6b69;
    --brand-green: #7cc242;
    --brand-green-dark: #2f6a12;
    --ink-light: #ececec;
    --ink-soft: #bdbdbd;
    --band-black: #0c0c0c;
    --band-white: #d8d8d4;
  }
  * { box-sizing: border-box; margin: 0; padding: 0; }
  html, body {
    width: 1200px; height: 900px; overflow: hidden;
    background: var(--page-bg);
  }
  .sheet {
    width: 1200px; height: 900px;
    display: flex; flex-direction: column; align-items: center; justify-content: center;
    gap: 24px;
  }
  .card {
    position: relative;
    width: 700px; height: 400px;
    border-radius: 26px;
    overflow: hidden;
    background: linear-gradient(160deg, var(--card-top), var(--card-bottom));
    box-shadow: inset 0 0 0 1px var(--card-edge);
  }
  .card-bands { position: absolute; inset: 0; }
  .brand-name {
    position: absolute;
    font-family: "Questrial", sans-serif;
    font-size: 44px;
    color: var(--brand-green);
    letter-spacing: 1px;
    white-space: nowrap;
  }
  .card--front .brand-name { left: 0; right: 0; top: 95px; text-align: center; }
  .card--back .brand-name { left: 0; right: 0; top: 140px; text-align: center; font-size: 50px; }
  .person-name {
    position: absolute; left: 60px; top: 205px;
    font-family: "Questrial", sans-serif;
    font-size: 28px; letter-spacing: 1px;
    color: var(--brand-green);
    padding-bottom: 6px;
    border-bottom: 1px solid #6f6f6d;
    width: 300px;
  }
  .contact {
    position: absolute;
    display: flex; align-items: center; gap: 10px;
    font-family: "Arimo", sans-serif;
    font-size: 17px; color: var(--ink-light);
  }
  .contact svg { width: 16px; height: 16px; flex: none; }
  .contact--mobile { left: 60px; top: 256px; }
  .contact--fax { left: 330px; top: 214px; }
  .contact--email { left: 90px; top: 282px; }
</style>
</head>
<body>
<main class="sheet">

  <section class="card card--front" aria-label="Business card front">
    <svg class="card-bands" viewBox="0 0 700 400" aria-hidden="true">
      <polygon points="360,318 700,246 700,260 380,318" fill="var(--brand-green)"/>
      <polygon points="0,322 380,318 700,262 700,292 420,350 0,360" fill="var(--band-black)"/>
      <polygon points="130,360 420,350 700,292 700,301 430,359 130,366" fill="var(--band-white)"/>
    </svg>

    <div class="brand-name">Northfield Builders</div>

    <div class="person-name">MARK ELLISON</div>

    <div class="contact contact--mobile">
      <svg viewBox="0 0 16 16"><rect x="4" y="1" width="8" height="14" rx="2" fill="var(--brand-green)"/><rect x="5.5" y="3" width="5" height="7" fill="var(--card-bottom)"/></svg>
      <span>xxxxxxxxxx</span>
    </div>
    <div class="contact contact--fax">
      <svg viewBox="0 0 16 16"><rect x="4" y="1" width="8" height="5" fill="var(--brand-green)"/><rect x="1" y="6" width="14" height="8" rx="1.5" fill="var(--brand-green)"/><rect x="4" y="10" width="8" height="2" fill="var(--card-bottom)"/></svg>
      <span>xxx xxx xxxx</span>
    </div>
    <div class="contact contact--email">
      <svg viewBox="0 0 16 16"><rect x="1.5" y="3.5" width="13" height="9" fill="none" stroke="var(--brand-green)" stroke-width="1.5"/><polyline points="1.5,3.5 8,9 14.5,3.5" fill="none" stroke="var(--brand-green)" stroke-width="1.5"/></svg>
      <span>name@Website.com</span>
    </div>
  </section>

  <section class="card card--back" aria-label="Business card back">
    <svg class="card-bands" viewBox="0 0 700 400" aria-hidden="true">
      <defs>
        <linearGradient id="green-band" x1="0" y1="0" x2="1" y2="0">
          <stop offset="0" stop-color="var(--brand-green-dark)"/>
          <stop offset="0.55" stop-color="var(--brand-green)"/>
          <stop offset="1" stop-color="var(--brand-green-dark)"/>
        </linearGradient>
      </defs>
      <polygon points="0,300 700,258 700,262 0,304" fill="var(--band-white)"/>
      <polygon points="0,312 700,270 700,322 0,364" fill="url(#green-band)"/>
    </svg>

    <div class="brand-name">Northfield Builders</div>
  </section>

</main>
</body>
</html>
```